Recto Verso Audiology Business Card

Business card with a beautiful design on the back. On the Recto you need the following data Lindqvist Oren Audiologist Hearing Solutions Hearing Protection Tinnitus Hyperacusis Tel: 0482/37 59 08 Email: On the back, you need something nice like the attached file. The logo "Corra Luna" can be in the center The colors of the Logo can not be changed If possible stay in the same colors as the logo Another solution is to put the logo on the front and have a nice back (A mosaic of small ears, hearing aids or other ..) Thank you _______________________________________________________________ Visit card On the Recto Lindqvist Oren Audiologist Hearing Solutions Hearing Protection Tinnitus Hyperacusis Tel: 0482/37 59 08 Email: You can put the logo " Corra Luna "on the Recto of the Verso The colors of the logo can not be changed. If you put the logo on the back, it must be well integrated. On the Verso I need something in the files. something stylish. It's a visit card for an audiologist. You can get ears of hearing aids if you need. Thanks

Target Market(s)

customers

Contact Information for Business Card

Carte de visite standard ou A6

Font styles to use
Serif
Sans Serif

Colors
33a6d7

Requirements
Must have
• the logo and a stylized background.
Nice to have
• It would be nice to have a back side related to audiology (ears, hearing aids etc.)

```html
<!DOCTYPE html>
<html lang="en">
<head>
<meta charset="utf-8">
<title>Corra Luna – Audiology Business Card</title>
<link rel="stylesheet" href="https://fonts.googleapis.com/css2?family=Encode+Sans+Semi+Condensed:wght@300;400&family=Fira+Sans:wght@300;400&display=swap">
<style>
  :root {
    --backdrop: #272727;
    --card: #161718;
    --card-edge: #0e0f10;
    --teal: #33a6d7;
    --teal-soft: #3fb8cf;
    --grey-muted: #4c5257;
    --text-light: #c9cdd0;
    --gold: #c9a336;
    --gold-deep: #7a5f17;
  }
  * { box-sizing: border-box; margin: 0; padding: 0; }
  html, body {
    width: 1200px;
    height: 601px;
    overflow: hidden;
    background: var(--backdrop);
  }
  .stage { position: relative; width: 1200px; height: 601px; }
  .card {
    position: absolute;
    top: 158px;
    height: 279px;
    background: var(--card);
    border-bottom: 3px solid var(--card-edge);
  }
  /* Recto */
  .card--front { left: 122px; width: 450px; }
  .brand-mark {
    position: absolute;
    left: 40px;
    top: 61px;
    width: 165px;
    height: 152px;
    display: flex;
    align-items: center;
    gap: 9px;
  }
  .brand-mark__square {
    width: 12px; height: 12px;
    background: var(--teal-soft);
    flex: none;
  }
  .brand-name {
    font-family: "Encode Sans Semi Condensed", sans-serif;
    font-weight: 300;
    font-size: 27px;
    letter-spacing: 0.5px;
    line-height: 1;
    color: var(--teal-soft);
    white-space: nowrap;
  }
  .contact {
    position: absolute;
    left: 236px;
    top: 58px;
    font-family: "Fira Sans", sans-serif;
  }
  .contact__name {
    font-family: "Encode Sans Semi Condensed", sans-serif;
    font-weight: 400;
    font-size: 17px;
    letter-spacing: 0.6px;
    text-transform: uppercase;
    color: var(--teal-soft);
    line-height: 1;
  }
  .contact__role {
    font-family: "Encode Sans Semi Condensed", sans-serif;
    font-weight: 300;
    font-size: 11px;
    letter-spacing: 0.6px;
    text-transform: uppercase;
    color: var(--grey-muted);
    margin-top: 4px;
  }
  .contact__details {
    list-style: none;
    margin-top: 18px;
    font-size: 10.5px;
    font-weight: 300;
    color: var(--text-light);
    line-height: 15px;
  }
  .services {
    list-style: none;
    margin-top: 13px;
    font-size: 10.5px;
    font-weight: 300;
    color: var(--text-light);
    line-height: 15px;
  }
  .services li { position: relative; padding-left: 11px; }
  .services li::before {
    content: "";
    position: absolute;
    left: 0; top: 6px;
    width: 4px; height: 4px;
    border-radius: 50%;
    background: var(--teal);
  }
  /* Verso */
  .card--back { left: 634px; width: 464px; overflow: hidden; }
  .ear-pattern {
    position: absolute;
    inset: 0;
    background: radial-gradient(ellipse at center, var(--gold-deep) 0%, #4a3a12 55%, #2b230d 100%);
  }
  .back-panel {
    position: absolute;
    left: 157px;
    top: 76px;
    width: 146px;
    height: 131px;
    background: var(--card);
    display: flex;
    align-items: center;
    justify-content: center;
  }
  .back-panel .brand-name { color: var(--gold); font-size: 25px; }
</style>
</head>
<body>
<main class="stage">
  <section class="card card--front" aria-label="Business card front">
    <div class="brand-mark">
      <span class="brand-mark__square"></span>
      <span class="brand-name">Corra Luna</span>
    </div>
    <div class="contact">
      <h1 class="contact__name">Lindqvist Oren</h1>
      <p class="contact__role">Audiologist Hearing</p>
      <ul class="contact__details">
        <li>0482/37 59 08</li>
        <li>info@corralunahearing.com</li>
        <li>www.corralunahearing.com</li>
      </ul>
      <ul class="services">
        <li>Solutions Hearing</li>
        <li>Protection</li>
        <li>Tinnitus</li>
        <li>Hyperacusis</li>
      </ul>
    </div>
  </section>

  <section class="card card--back" aria-label="Business card back">
    <div class="ear-pattern" role="img" aria-label="Repeating gold pattern of small ears with sound waves on black"></div>
    <div class="back-panel">
      <span class="brand-name">Corra Luna</span>
    </div>
  </section>
</main>
</body>
</html>
```